Allied Health team of Physiotherapists & Occupational Therapists seek a business card design

We have our new logo, we now need our new business cards and stationary. Tidewell: Oedema & Family Clinic is seeking a generic card design to represent our whole team and individual cards for each therapist that incorporates our new logo to communicate our holistic approach that is calming, nuturing, supportive and welcoming.
Our Physiotherapists and Occupational Therapists assess, treat and provide education for people who are at risk of or who have lymphoedema. This is often as a result of treatment for cancer. We provide pre-operative and post-operative management and cancer rehabilitation in our Pilates studio. Our team also consists of Physiotherapists who have a strong interest in pelvic floor and continence management for both men and women.

Target Market(s)

Mainly women health conscious

Industry/Entity Type

Allied Health: Physiotherapy / Occupational Therapy

Contact Information for Business Card

Address: 14 Gallivant Ave Seabrook 3210 Phone: 84316570 fax: 8431 6578 Email: info@tidewellcareservices.com.au Website: tidewellcareservices.com.au Facebook address: facebook.com/TidewellOedemaAndFamilyCareClinic. Room to write appointments. Individual cards need to have name, office email and individual email and professional details

Requirements
Must have
• Logo as per uploaded documents

```html
<!DOCTYPE html>
<html lang="en">
<head>
<meta charset="utf-8">
<title>Tidewell Business Cards</title>
<link href="https://fonts.googleapis.com/css2?family=Alike&family=Figtree:wght@400;600&display=swap" rel="stylesheet">
<style>
  :root{
    --backdrop:#121214;
    --peach-deep:#f9ae80;
    --peach-light:#fdd0aa;
    --salmon:#f3977a;
    --cream:#fffbd6;
    --sage:#c2cbbd;
    --ink:#33363a;
    --ink-soft:#4a4e54;
    --white:#fff8f2;
    --lilac:#c6a6d8;
  }
  html,body{margin:0;padding:0;width:1200px;height:886px;overflow:hidden;background:var(--backdrop);}
  .canvas{position:relative;width:1200px;height:886px;}
  .card{position:absolute;width:447px;height:255px;overflow:hidden;box-shadow:0 18px 40px rgba(0,0,0,.55);}
  .card svg.shape{position:absolute;inset:0;}
  .card-front{left:223px;top:141px;}
  .card-back{left:530px;top:488px;}

  .holder-name{position:absolute;left:16px;top:28px;margin:0;font-family:"Alike",serif;font-size:23px;font-weight:400;letter-spacing:.6px;color:var(--ink);}
  .holder-role{position:absolute;left:16px;top:58px;margin:0;font-family:"Figtree",sans-serif;font-size:11.5px;color:var(--ink-soft);}
  .credentials{position:absolute;left:16px;top:118px;margin:0;padding:0;list-style:none;font-family:"Figtree",sans-serif;font-size:9.6px;line-height:15px;color:var(--ink-soft);letter-spacing:-.1px;}
  .specialties{position:absolute;left:16px;top:196px;margin:0;padding:0;list-style:none;font-family:"Figtree",sans-serif;font-size:9.6px;line-height:15px;font-weight:600;color:var(--ink);}

  .clinic-mark{position:absolute;left:295px;top:60px;width:136px;height:136px;border-radius:50%;background:var(--cream);border:4px solid var(--sage);box-sizing:border-box;display:flex;align-items:center;justify-content:center;}
  .clinic-mark span{font-family:"Figtree",sans-serif;font-size:21px;font-weight:400;color:var(--peach-deep);}

  .clinic-photo{position:absolute;left:0;top:0;width:447px;height:120px;background:linear-gradient(100deg,#b58cc9 0%,#e9c3cf 25%,#f3cfd2 45%,#d9b3e2 65%,var(--lilac) 100%);}

  .contacts{position:absolute;left:17px;top:101px;margin:0;padding:0;list-style:none;font-family:"Figtree",sans-serif;font-size:11.3px;color:var(--white);}
  .contacts li{display:flex;align-items:center;height:17px;}
  .contacts .phone-number{letter-spacing:1.4px;font-size:12px;}
  .contacts svg{width:12px;height:12px;margin-right:6px;flex:none;}
  .next-appointment{position:absolute;left:240px;top:227px;margin:0;font-family:"Figtree",sans-serif;font-size:11.3px;color:var(--white);}
  .next-appointment .write-line{display:inline-block;width:70px;border-bottom:1px dotted var(--white);margin-left:3px;}
</style>
</head>
<body>
<main class="canvas">

  <section class="card card-front" aria-label="Business card front">
    <svg class="shape" width="447" height="255" viewBox="0 0 447 255">
      <defs>
        <linearGradient id="frontPeach" x1="0" x2="1" y1="0" y2="0">
          <stop offset="0" stop-color="var(--peach-deep)"/>
          <stop offset="1" stop-color="var(--peach-light)"/>
        </linearGradient>
      </defs>
      <rect width="447" height="255" fill="var(--cream)"/>
      <path d="M0 0H447V110C400 122 330 126 290 118C200 100 90 82 0 94Z" fill="url(#frontPeach)"/>
      <path d="M0 94C90 82 200 100 290 118C330 126 400 122 447 110V114C400 127 330 131 290 123C200 106 90 90 0 100Z" fill="var(--sage)"/>
    </svg>
    <h1 class="holder-name">Maren Ashcombe</h1>
    <p class="holder-role">Physiotherapist</p>
    <ul class="credentials">
      <li>B. Physio (Hons), B.App.Sci. (Human Movement/Psych)</li>
      <li>Post Grad Certif. Exercise for Women</li>
      <li>Post Grad Certif. Continence &amp; Pelvic Floor</li>
      <li>Rehabilitation</li>
    </ul>
    <ul class="specialties">
      <li>Lymphoedema &amp; Oncology Rehabilitation</li>
      <li>Continence &amp; Pelvic Floor</li>
    </ul>
    <div class="clinic-mark"><span>Tidewell</span></div>
  </section>

  <section class="card card-back" aria-label="Business card back">
    <svg class="shape" width="447" height="255" viewBox="0 0 447 255">
      <defs>
        <linearGradient id="backSalmon" x1="0" x2="1" y1="0" y2="0">
          <stop offset="0" stop-color="var(--peach-deep)"/>
          <stop offset="1" stop-color="var(--salmon)"/>
        </linearGradient>
      </defs>
      <rect width="447" height="255" fill="url(#backSalmon)"/>
    </svg>
    <div class="clinic-photo" role="img" aria-label="Photo of a therapist in a lilac uniform in a pilates studio"></div>
    <svg class="shape" width="447" height="255" viewBox="0 0 447 255">
      <path d="M0 76C80 62 150 80 235 112C300 134 400 120 447 104V255H0Z" fill="url(#backSalmon)"/>
      <path d="M0 72C80 58 150 76 235 108C300 130 400 116 447 100V104C400 120 300 134 235 112C150 80 80 62 0 76Z" fill="var(--sage)"/>
    </svg>
    <ul class="contacts">
      <li><svg viewBox="0 0 12 12"><circle cx="6" cy="6" r="5.5" fill="none" stroke="var(--white)" stroke-width=".8"/><path d="M4 3.2l1 1.6-.6.7c.4.9 1 1.5 1.9 1.9l.7-.6 1.6 1-.6 1C5.8 8.8 3.2 6.2 3 4z" fill="var(--white)"/></svg><span class="phone-number">8431 6570</span></li>
      <li><svg viewBox="0 0 12 12"><circle cx="6" cy="6" r="5.5" fill="none" stroke="var(--white)" stroke-width=".8"/><rect x="3.5" y="4.5" width="5" height="4" fill="none" stroke="var(--white)" stroke-width=".8"/><rect x="4.5" y="3" width="3" height="1.5" fill="var(--white)"/></svg><span class="phone-number">8431 6578</span></li>
      <li><svg viewBox="0 0 12 12"><circle cx="6" cy="6" r="5.5" fill="none" stroke="var(--white)" stroke-width=".8"/><rect x="3" y="4" width="6" height="4" fill="none" stroke="var(--white)" stroke-width=".8"/><path d="M3 4l3 2.2L9 4" fill="none" stroke="var(--white)" stroke-width=".8"/></svg>info@tidewellcareservices.com.au</li>
      <li><svg viewBox="0 0 12 12"><circle cx="6" cy="6" r="5.5" fill="none" stroke="var(--white)" stroke-width=".8"/></svg>TidewellOedemaAndFamilyCareClinic</li>
      <li><svg viewBox="0 0 12 12"><circle cx="6" cy="6" r="5.5" fill="none" stroke="var(--white)" stroke-width=".8"/><circle cx="6" cy="6" r="3" fill="none" stroke="var(--white)" stroke-width=".7"/><path d="M3 6h6M6 3v6" stroke="var(--white)" stroke-width=".6"/></svg>tidewellcareservices.com.au</li>
      <li><svg viewBox="0 0 12 12"><circle cx="6" cy="6" r="5.5" fill="none" stroke="var(--white)" stroke-width=".8"/><path d="M6 9.5C4.5 7.6 3.8 6.4 3.8 5.2a2.2 2.2 0 014.4 0c0 1.2-.7 2.4-2.2 4.3z" fill="var(--white)"/></svg>14 Gallivant Ave, Seabrook 3210</li>
    </ul>
    <p class="next-appointment">Next Appointment<span class="write-line"></span></p>
  </section>

</main>
</body>
</html>
```